Facebook post - Kestrel Bay Finishes has arrived to make your tiles smile!

Kestrel Bay Finishes would like to release a Facebook post calling out to the market that we have arrived. The company has a new and fresh branding aiming for a female demographic between the ages of 40 and 55 located in the South West of Western Australia. The company image MUST be centered around trust! Our Primary aim is to create an uncompromising trust from the very first impression. Our logo tag line is, 'We love to make your tiles smile'.
I need 5 x facebook template designs and also 5 x posts.
Our 1st campaign is to be 5 x posts centered around the arrival of this fantastic new company.
We are company that provides the services of:
- Grout and silicone repair.
- Broken or drummy tile replacement and;
- Grout sealing
Dont forget that we must communicate TRUST and the we love to make your tiles SMILE!

```html
<!DOCTYPE html>
<html lang="en">
<head>
<meta charset="utf-8">
<title>Kestrel Bay Finishes – Launch Post Set</title>
<link href="https://fonts.googleapis.com/css2?family=Oswald:wght@400;500;600&family=Lato:wght@400;700&display=swap" rel="stylesheet">
<style>
  :root {
    --ink: #2a2a2c;
    --ink-soft: #3a3a3d;
    --blue: #2e9ad8;
    --paper: #f1f1f1;
    --white: #ffffff;
    --photo-dark-a: #3d3935;
    --photo-dark-b: #1f1d1b;
    --photo-light-a: #d9d4cc;
    --photo-light-b: #a89f94;
  }
  * { box-sizing: border-box; margin: 0; padding: 0; }
  html, body { width: 1200px; height: 3308px; overflow: hidden; background: var(--white); }
  body { position: relative; font-family: 'Lato', sans-serif; }

  .post { position: absolute; left: 40px; width: 1120px; height: 590px; overflow: hidden; background: var(--paper); }
  .post-1 { top: 40px; }
  .post-2 { top: 690px; }
  .post-3 { top: 1340px; background: var(--ink); }
  .post-4 { top: 1990px; }
  .post-5 { top: 2650px; }

  .abs { position: absolute; }
  .dark-block { background: var(--ink); }
  .photo-dark { background: linear-gradient(135deg, var(--photo-dark-a), var(--photo-dark-b)); }
  .photo-light { background: linear-gradient(160deg, var(--photo-light-a), var(--photo-light-b)); }
  .photo-tile { background: linear-gradient(140deg, #9a9a9a, #6f7377 60%, #c9c9c9); }

  .headline { font-family: 'Oswald', sans-serif; font-weight: 500; text-transform: uppercase; line-height: 1.05; letter-spacing: 1px; white-space: nowrap; }
  .headline-blue { color: var(--blue); }
  .headline-ink { color: var(--ink); }
  .subhead { font-family: 'Oswald', sans-serif; font-weight: 600; color: var(--white); font-size: 44px; line-height: 1.1; letter-spacing: 1px; }
  .body-copy { font-size: 19px; line-height: 1.35; color: var(--white); }
  .body-copy.ink { color: var(--ink); }

  .callout { position: absolute; width: 360px; padding: 20px 24px; background: var(--ink); border: 4px solid var(--blue); color: var(--white); font-family: 'Oswald', sans-serif; font-size: 21px; line-height: 1.3; }
  .callout .accent { color: var(--blue); }

  .brand { position: absolute; display: flex; align-items: center; gap: 14px; }
  .brand-dot { width: 44px; height: 44px; border-radius: 50%; background: var(--blue); }
  .brand-name { font-family: 'Oswald', sans-serif; font-weight: 500; font-size: 32px; color: var(--blue); letter-spacing: 1px; text-transform: uppercase; }

  .stripes { position: absolute; display: flex; gap: 9px; }
  .stripes span { display: block; width: 9px; height: 32px; background: var(--ink); }
  .stripes.blue span { background: var(--blue); height: 22px; }
  .stripes.white span { background: var(--white); }

  .service-card { background: var(--white); padding: 36px 30px 30px 46px; }
  .service-card .card-bar { position: absolute; left: 0; top: 30px; width: 10px; height: 130px; background: var(--blue); }
  .service-card .card-label { font-size: 13px; font-weight: 700; letter-spacing: 1px; color: var(--ink); margin-bottom: 18px; }
  .service-list { list-style: none; }
  .service-list li { font-family: 'Oswald', sans-serif; font-size: 27px; color: var(--ink); margin-bottom: 18px; padding-left: 22px; position: relative; }
  .service-list li::before { content: ""; position: absolute; left: 0; top: 8px; width: 10px; height: 24px; background: var(--blue); }

  .frame-line { position: absolute; border: 3px solid var(--white); }
</style>
</head>
<body>

<!-- Post 1: Grout & Silicone -->
<section class="post post-1">
  <svg class="abs" style="left:30px;top:14px" width="60" height="30" viewBox="0 0 60 30"><path d="M0 30 L14 0 M16 30 L30 0 M32 30 L46 0" stroke="var(--blue)" stroke-width="6"/></svg>
  <div class="abs dark-block" style="left:40px;top:40px;width:1040px;height:330px;"></div>
  <h1 class="abs headline headline-blue" style="left:90px;top:60px;font-size:64px;">Grout &amp; Silicone</h1>
  <p class="abs subhead" style="left:96px;top:140px;">Rejuvenation</p>
  <p class="abs body-copy" style="left:96px;top:250px;width:300px;">Dont forget that we must communicate <span style="color:var(--blue)">TRUST</span> and the we love to make your tiles <span style="color:var(--blue)">SMILE!</span></p>
  <div class="abs service-card" style="left:420px;top:160px;width:360px;height:370px;">
    <span class="card-bar"></span>
    <p class="card-label">WHAT WE DO</p>
    <ul class="service-list">
      <li>Grout Repair</li>
      <li>Grout Sealing</li>
      <li>Silicone Replacement</li>
      <li>Obligation Free Quotes</li>
    </ul>
  </div>
  <div class="abs photo-tile" role="img" aria-label="Close-up photo of tiles with fresh grout lines" style="left:780px;top:160px;width:340px;height:370px;"></div>
  <div class="brand" style="left:60px;top:470px;"><span class="brand-dot"></span><span class="brand-name">Kestrel Bay Finishes</span></div>
  <div class="stripes" style="left:830px;top:548px;"><span></span><span></span><span></span><span></span><span></span><span></span><span></span><span></span><span></span><span></span><span></span><span></span></div>
</section>

<!-- Post 2: Broken or Drummy Tile -->
<section class="post post-2">
  <div class="abs photo-dark" role="img" aria-label="Photo of a dimly lit tiled bathroom with towels and a vanity" style="left:0;top:30px;width:780px;height:540px;"></div>
  <div class="frame-line" style="left:90px;top:40px;width:220px;height:150px;border-color:rgba(255,255,255,.5)"></div>
  <h2 class="abs headline headline-blue" style="left:200px;top:170px;font-size:48px;">Broken or Drummy Tile</h2>
  <p class="abs subhead" style="left:200px;top:232px;">Replacement</p>
  <p class="abs body-copy" style="left:200px;top:300px;width:340px;">Lorem ipsum dolor sit amet, consectetuer adipiscing elit. Aenean commodo ligula eget</p>
  <svg class="abs" style="left:20px;top:270px" width="40" height="100" viewBox="0 0 40 100"><path d="M0 20 L40 0 M0 45 L40 25 M0 70 L40 50 M0 95 L40 75" stroke="var(--white)" stroke-width="6"/></svg>
  <div class="brand" style="left:40px;top:480px;"><span class="brand-dot"></span><span class="brand-name">Kestrel Bay Finishes</span></div>
  <div class="stripes blue" style="left:960px;top:30px;"><span></span><span></span><span></span><span></span><span></span><span></span><span></span></div>
  <div class="callout" style="left:740px;top:390px;">Dont forget that we must communicate <span class="accent">TRUST</span> and the we love to make your tiles <span class="accent">SMILE!</span></div>
</section>

<!-- Post 3: Grout Sealing -->
<section class="post post-3">
  <div class="abs" style="left:0;top:0;width:1120px;height:40px;background:var(--paper)"></div>
  <div class="abs photo-light" role="img" aria-label="Photo of a bright bathroom with vanity basin and mirror" style="left:560px;top:70px;width:540px;height:460px;"></div>
  <div class="abs" style="left:0;top:80px;width:570px;height:290px;background:var(--blue)"></div>
  <h2 class="abs headline headline-ink" style="left:90px;top:110px;font-size:72px;">Grout Sealing</h2>
  <p class="abs body-copy" style="left:90px;top:220px;width:380px;">Lorem ipsum dolor sit amet, consectetuer adipiscing elit. Aenean commodo ligula eget</p>
  <svg class="abs" style="left:400px;top:340px" width="120" height="24" viewBox="0 0 120 24"><path d="M0 24 L12 0 M22 24 L34 0 M44 24 L56 0 M66 24 L78 0 M88 24 L100 0" stroke="var(--white)" stroke-width="6"/></svg>
  <div class="brand" style="left:40px;top:460px;"><span class="brand-dot"></span><span class="brand-name">Kestrel Bay Finishes</span></div>
  <div class="stripes blue" style="left:960px;top:10px;"><span></span><span></span><span></span><span></span><span></span><span></span><span></span></div>
  <div class="callout" style="left:730px;top:400px;">Dont forget that we must communicate <span class="accent">TRUST</span> and the we love to make your tiles <span class="accent">SMILE!</span></div>
</section>

<!-- Post 4: Lorem Ipsum light -->
<section class="post post-4">
  <div class="stripes" style="left:12px;top:60px;flex-direction:column;gap:8px;"><span style="width:22px;height:8px"></span><span style="width:22px;height:8px;background:var(--blue)"></span><span style="width:22px;height:8px"></span><span style="width:22px;height:8px;background:var(--blue)"></span></div>
  <h2 class="abs headline headline-ink" style="left:80px;top:30px;font-size:74px;">Lorem Ipsum</h2>
  <p class="abs body-copy ink" style="left:80px;top:120px;width:400px;">Lorem ipsum dolor sit amet, consectetuer adipiscing elit. Aenean commodo ligula eget</p>
  <div class="abs photo-light" role="img" aria-label="Photo of a bathroom vanity with towels and glass shower" style="left:640px;top:20px;width:470px;height:280px;"></div>
  <div class="abs photo-light" role="img" aria-label="Photo of a tiled bathroom with wall basin and niche shelf" style="left:60px;top:240px;width:420px;height:330px;background:linear-gradient(170deg,#e4e0da,#b9b2a8)"></div>
  <div class="callout" style="left:450px;top:260px;">Dont forget that we must communicate <span class="accent">TRUST</span> and the we love to make your tiles <span class="accent">SMILE!</span></div>
  <div class="brand" style="left:690px;top:480px;"><span class="brand-dot"></span><span class="brand-name">Kestrel Bay Finishes</span></div>
  <div class="abs" style="left:1100px;top:320px;width:8px;height:230px;background:var(--blue)"></div>
</section>

<!-- Post 5: Lorem Ipsum dark -->
<section class="post post-5">
  <div class="abs photo-dark" role="img" aria-label="Photo of a modern bathroom with marble-look wall tiles and timber cabinetry" style="left:0;top:0;width:1120px;height:430px;background:linear-gradient(120deg,#5a544d,#2c2926 55%,#6b645c)"></div>
  <div class="abs" style="left:40px;top:30px;width:520px;height:200px;background:rgba(30,30,32,.75)"></div>
  <h2 class="abs headline headline-blue" style="left:90px;top:50px;font-size:70px;">Lorem Ipsum</h2>
  <p class="abs body-copy" style="left:90px;top:140px;width:400px;">Lorem ipsum dolor sit amet, consectetuer adipiscing elit. Aenean commodo ligula eget</p>
  <div class="abs" style="left:0;top:430px;width:1120px;height:160px;background:var(--paper)"></div>
  <div class="abs dark-block" style="left:0;top:360px;width:60px;height:230px;"></div>
  <div class="stripes white" style="left:18px;top:420px;flex-direction:column;gap:8px;"><span style="width:24px;height:8px"></span><span style="width:24px;height:8px"></span><span style="width:24px;height:8px"></span></div>
  <div class="callout" style="left:90px;top:420px;">Dont forget that we must communicate <span class="accent">TRUST</span> and the we love to make your tiles <span class="accent">SMILE!</span></div>
  <div class="brand" style="left:690px;top:500px;"><span class="brand-dot"></span><span class="brand-name">Kestrel Bay Finishes</span></div>
</section>

</body>
</html>
```